Letterhead for Business Law Firm

We need a letter head for our firm based on the design we have settled on and it is attached. Our clients are small and large businesses around the world, and our letterhead is used typically for formal legal purposes such as demand letters (accusing the recipient of doing bad things) or responding to demand letters. It may also be sent to regulators and other government agencies. So this needs to be tasteful, but a little edgy as well - we try to convey that we are a firm that is different - businesses and investors come to us for creative, quick advice, typically in high stress circumstances, and for our ability to work through high conflict situations, and rapid paced engagements.

Target Market(s)

Lawyers, business executives, investors, government regulators who may receive letters from this firm on behalf of its clients.

Industry/Entity Type

Business

Requirements
Must have
• The design and the firm's contact information:
• Thornwell Law Firm, P.C.
• 1876 NE 57th Ave
• Portland, OR 97213
• phone: 971 555 0147
• fax: 971 555 0182
• in what placement and how depicted (e.g. a phone icon instead of the word "phone") I leave to your creative ideas.
Nice to have
• design and information can be placed at the top, bottom and/or sides of the letter, and the design should be for a standard letter size paper - and can have a separate design for the second page.

```html
<!DOCTYPE html>
<html lang="en">
<head>
<meta charset="utf-8">
<title>Thornwell Letterhead</title>
<link rel="stylesheet" href="https://fonts.googleapis.com/css2?family=PT+Sans:wght@400;700&display=swap">
<style>
  :root {
    --paper: #ffffff;
    --ink: #3a3a3a;
    --rule: #9a9a9a;
    --teal: #4a7b80;
    --night: #1c1819;
    --brand: #1c1819;
  }
  html, body {
    margin: 0;
    padding: 0;
    width: 1019px;
    height: 1200px;
    overflow: hidden;
    background: var(--paper);
  }
  .letterhead {
    position: relative;
    width: 1019px;
    height: 1200px;
    background: var(--paper);
    font-family: "PT Sans", sans-serif;
    color: var(--ink);
  }
  .brand {
    position: absolute;
    left: 57px;
    top: 50px;
    display: flex;
    align-items: center;
    gap: 14px;
  }
  .brand-square {
    width: 22px;
    height: 22px;
    background: var(--teal);
  }
  .brand-name {
    font-family: "PT Sans", sans-serif;
    font-weight: 400;
    font-size: 52px;
    letter-spacing: 9px;
    line-height: 1;
    color: var(--brand);
  }
  .contact {
    position: absolute;
    left: 812px;
    top: 35px;
    height: 100px;
    padding-left: 15px;
    border-left: 1px solid var(--rule);
    font-size: 15px;
    line-height: 17px;
  }
  .contact-address {
    margin: 0 0 13px;
  }
  .contact-list {
    list-style: none;
    margin: 0;
    padding: 0;
  }
  .contact-list li {
    display: flex;
    align-items: center;
    gap: 5px;
    line-height: 19px;
  }
  .contact-icon {
    width: 11px;
    height: 11px;
    fill: var(--ink);
    flex: none;
  }
  .footer-wave {
    position: absolute;
    left: 0;
    bottom: 0;
    width: 1019px;
    height: 119px;
    display: block;
  }
  .footer-web {
    position: absolute;
    left: 736px;
    top: 1165px;
    font-size: 16px;
    letter-spacing: 3.2px;
    color: var(--paper);
  }
</style>
</head>
<body>
<main class="letterhead">
  <header>
    <div class="brand">
      <span class="brand-square"></span>
      <span class="brand-name">THORNWELL</span>
    </div>
    <address class="contact" style="font-style:normal">
      <p class="contact-address">1876 NE 57th Ave<br>Portland, OR 97213</p>
      <ul class="contact-list">
        <li>
          <svg class="contact-icon" viewBox="0 0 12 12" aria-label="Phone"><path d="M2.5 0.5 L4.5 0.5 L5.3 3.2 L4 4.2 C4.6 5.8 6.2 7.4 7.8 8 L8.8 6.7 L11.5 7.5 L11.5 9.5 C11.5 10.8 10.6 11.5 9.5 11.5 C4.5 11 1 7.5 0.5 2.5 C0.5 1.4 1.2 0.5 2.5 0.5 Z"/></svg>
          971 555 0147
        </li>
        <li>
          <svg class="contact-icon" viewBox="0 0 12 12" aria-label="Fax"><rect x="3" y="0.5" width="6" height="3.5"/><rect x="0.5" y="4.5" width="11" height="5" rx="1"/><rect x="3" y="8" width="6" height="3.5" fill="#fff" stroke="#3a3a3a" stroke-width="1"/></svg>
          971 555 0182
        </li>
        <li>
          <svg class="contact-icon" viewBox="0 0 12 12" aria-label="Email"><path d="M0.5 5 L6 1 L11.5 5 L11.5 11 L0.5 11 Z"/><path d="M1.5 5.6 L6 8.6 L10.5 5.6" fill="none" stroke="#fff" stroke-width="1"/></svg>
          info@thornwell.com
        </li>
      </ul>
    </address>
  </header>

  <footer>
    <svg class="footer-wave" viewBox="116 1285 1027 132" preserveAspectRatio="none" aria-hidden="true">
      <path fill="var(--teal)" d="M116 1295 C200 1330 300 1360 480 1365 C700 1362 900 1336 1143 1378 L1143 1417 L116 1417 Z"/>
      <path fill="var(--paper)" d="M116 1343 C250 1375 400 1380 560 1370 C750 1357 900 1345 1010 1350 C1080 1355 1120 1367 1143 1380 L1143 1417 L116 1417 Z"/>
      <path fill="var(--night)" d="M116 1348 C250 1380 400 1385 560 1375 C750 1362 900 1350 1010 1355 C1080 1360 1120 1372 1143 1385 L1143 1417 L116 1417 Z"/>
    </svg>
    <div class="footer-web">www.thornwell.com</div>
  </footer>
</main>
</body>
</html>
```